Professional Website

We are looking for a new website for our Staffing Company. Attached is a document with all the details and pages needed along with some examples of others websites.

We want a professional Look and feel around the same color theme as the attached Amber Compass.

We currently host our site on PageLoom.io. If the winning designer can also add to PageLoom, that is a plus.

```html
<!DOCTYPE html>
<html lang="en">
<head>
<meta charset="utf-8">
<title>Quillbrook – Website Homepage</title>
<link href="https://fonts.googleapis.com/css2?family=Lato:wght@400;700&display=swap" rel="stylesheet">
<style>
:root{
  --board:#333333;
  --navy:#1d1f8c;
  --blue:#2233b8;
  --ink:#1a1a1a;
  --muted:#707070;
  --field:#ececec;
  --soft:#f4f4f4;
  --black:#000000;
  --white:#ffffff;
}
*{box-sizing:border-box;margin:0;padding:0}
html,body{width:939px;height:1200px;overflow:hidden;background:var(--board);font-family:"Lato",sans-serif;color:var(--ink)}
.page{position:absolute;top:56.6px;width:702px;background:var(--white);transform:scale(.55);transform-origin:0 0;overflow:hidden}
.page--home{left:61.6px;height:1976px}
.page--short{left:491.7px;height:1049px}
.abs{position:absolute}
.topbar{left:0;top:0;width:702px;height:24px;background:var(--navy);color:var(--white);font-size:9px;font-weight:700}
.topbar span{position:absolute;top:7px;display:flex;align-items:center;gap:5px}
.nav{left:0;top:24px;width:702px;height:47px;background:var(--white)}
.brand{position:absolute;font-weight:700;color:var(--navy);font-size:30px;letter-spacing:-.5px}
.nav a{position:absolute;top:20px;font-size:9px;color:var(--ink);text-decoration:none}
.nav a.active{color:var(--navy)}
.pill{position:absolute;display:flex;align-items:center;justify-content:center;border-radius:16px;background:var(--navy);color:var(--white);font-size:9px;font-weight:700}
.pill--light{background:var(--white);color:var(--navy)}
.hero{left:0;top:71px;width:702px;height:410px;overflow:hidden}
.hero-photo{position:absolute;left:0;top:0;width:702px;height:380px;background:linear-gradient(120deg,#3a4a63 0%,#6b5040 35%,#c9c3bb 60%,#5e4030 80%,#2a2f3c 100%)}
.hero-copy{position:absolute;left:0;width:702px;text-align:center;color:var(--white)}
.center{text-align:center;left:0;width:702px}
.about-photo{left:65px;top:471px;width:216px;height:259px;background:linear-gradient(160deg,#8a8c92,#4a4d55 55%,#2d3038)}
.about-text{left:305px;top:510px;width:260px;font-size:8.3px;line-height:15px;text-align:justify;color:#444}
.vlabel{writing-mode:vertical-rl;font-weight:700}
.core-copy{color:var(--white)}
.value{position:absolute;top:1199px;width:140px;text-align:center}
.value .icon{width:57px;height:57px;margin:0 auto;border-radius:50%;background:#f0f0f2;display:flex;align-items:center;justify-content:center}
.value h3{font-size:12px;font-weight:700;margin-top:19px}
.value p{font-size:8.5px;line-height:15px;color:var(--muted);margin:6px auto 0;width:130px;height:60px}
.value a{display:block;font-size:8.5px;color:var(--navy);font-weight:700;text-decoration:none;margin-top:4px}
.contact{left:0;top:1420px;width:702px;height:360px;background:var(--soft)}
.field{position:absolute;left:322px;width:286px;height:33px;background:var(--field);font-size:8.5px;color:#555;padding:12px 17px}
.info{position:absolute;left:93px;font-size:8.5px;line-height:14px}
.info b{display:block;color:var(--ink)}
.footer{left:0;width:702px;height:294px;color:var(--white)}
.footer h4{position:absolute;top:117px;font-size:12px;font-weight:700}
.footer ul{position:absolute;top:142px;list-style:none;font-size:8.5px;line-height:17.5px}
.footer .brand{color:var(--blue);left:65px;top:112px}
.social{position:absolute;top:185px;left:493px;display:flex;gap:7px}
.social i{width:7px;height:7px;border-radius:50%;background:var(--white);display:block}
</style>
</head>
<body>

<!-- Full homepage -->
<div class="page page--home">
  <div class="abs topbar">
    <span style="left:67px"><svg width="9" height="9" viewBox="0 0 10 10"><path d="M2 1l2 2-1 1.5a6 6 0 0 0 2.5 2.5L7 6l2 2-1.5 1.5C4.5 9 1 5.5.5 2.5z" fill="none" stroke="#fff"/></svg>555-014-2290</span>
    <span style="left:443px"><svg width="10" height="8"><rect x=".5" y=".5" width="9" height="7" fill="none" stroke="#fff"/></svg>Pay Card Login</span>
    <span style="left:552px"><svg width="10" height="9"><path d="M0 3L5 0 10 3zM1 8h8M2 4v3M5 4v3M8 4v3" stroke="#fff" fill="#fff"/></svg>Partner Bank Login</span>
  </div>
  <div class="abs nav">
    <div class="brand" style="left:65px;top:5px">Quillbrook</div>
    <a class="active" style="left:313px">Home</a><a style="left:365px">Jobs</a><a style="left:411px">About</a><a style="left:463px">Contact</a>
    <div class="pill" style="left:539px;top:11px;width:98px;height:29px">Employee Login</div>
  </div>
  <div class="abs hero">
    <div class="hero-photo" role="img" aria-label="Photo of hands holding a document over a desk"></div>
    <svg class="abs" style="left:0;top:0" width="702" height="410" viewBox="0 0 702 410">
      <polygon points="0,351 385,335 702,404 702,412 0,412" fill="#fff"/>
      <polygon points="385,335 702,318 702,404" fill="#1d1f8c"/>
      <polygon points="385,335 702,330 702,352" fill="#2233b8"/>
    </svg>
    <div class="hero-copy" style="top:81px;font-size:11px;font-weight:700">Welcome To</div>
    <div class="hero-copy" style="top:100px;font-size:25px;font-weight:700">Quillbrook Clearical &amp; Industrial</div>
    <div class="hero-copy" style="top:138px;font-size:8.5px;line-height:15px">Lorem ipsum dolor sit amet, consectetur adipiscing elit, sed do eiusmod tempor<br>incididunt ut labore et dolore magna aliqua.</div>
    <div class="pill" style="left:238px;top:177px;width:108px;height:29px">I'm looking for a Job</div>
    <div class="pill pill--light" style="left:356px;top:177px;width:107px;height:29px">I need Employees</div>
  </div>
  <div class="abs about-photo" role="img" aria-label="Photo of business people with network icons overlay"></div>
  <p class="abs about-text">Greatest part of our daily job is that we are constantly bringing people together. Our Clients come to us in search of the perfect candidate and the job hunters approach us when they are in need of a job or looking for their next exciting role. Being able to work with and connect the two is incredibly satisfying. Not to mention that in today's current job market, employers are fighting for the top talent. This makes our employees and partners grateful for the help in finding it!</p>
  <div class="pill" style="left:305px;top:640px;width:86px;height:30px">Learn More</div>
  <div class="abs vlabel" style="left:615px;top:494px;font-size:22px">ABOUT</div>
  <div class="abs vlabel" style="left:603px;top:494px;font-size:6.5px">CLERICAL &amp; INDUSTRIAL</div>
  <div class="abs" style="left:603px;top:608px;width:4px;height:54px;background:var(--navy)"></div>

  <svg class="abs" style="left:0;top:755px" width="702" height="340" viewBox="0 0 702 340" role="img" aria-label="Photo of a team joining hands with recruitment icons overlay">
    <defs><linearGradient id="coreTone" x1="0" y1="0" x2="1" y2="1"><stop offset="0" stop-color="#6a5a4e"/><stop offset=".5" stop-color="#8a7462"/><stop offset="1" stop-color="#3c3a40"/></linearGradient></defs>
    <polygon points="0,0 245,57 0,50" fill="#1d1f8c"/>
    <polygon points="0,50 245,57 0,85" fill="#2233b8"/>
    <polygon points="0,85 245,57 702,10 702,255 500,282 0,337" fill="url(#coreTone)"/>
    <polygon points="500,282 702,255 702,325" fill="#1d1f8c"/>
  </svg>
  <div class="abs center core-copy" style="top:857px;font-size:19px;font-weight:700">Core Business Activities</div>
  <p class="abs core-copy" style="left:91px;top:892px;width:520px;font-size:8.3px;line-height:15px;text-align:center">We are the leading recruiting agency for long-term staffing services. Quillbrook's recruiters put in the extra time and effort to send only the most qualified candidates to select positions. We raise the bar for other recruiting agencies as our performance continues to model that by connecting hardworking employees with long-term assignments, both businesses and families benefit immensely. Our business partners save time and resources as well as avoid unnecessary turnover.</p>
  <div class="pill" style="left:307px;top:965px;width:86px;height:30px">Learn More</div>

  <div class="abs center" style="top:1117px;font-size:19px">Our Values</div>
  <p class="abs center" style="top:1150px;font-size:7px;line-height:15px">Lorem ipsum dolor sit amet, consectetur adipiscing elit, sed do eiusmod tempor incididunt ut labore et dolore<br>magna aliqua. Quis ipsum suspendisse ultrices gravida. Risus commodo</p>
  <div class="value" style="left:52px"><div class="icon"><svg width="26" height="26"><circle cx="13" cy="13" r="8" fill="none" stroke="#1d1f8c" stroke-width="1.5"/></svg></div><h3>Team Players</h3><p>We're always willing to go the extra mile for the office, share the workload, and coach one another for success.</p><a>Learn More</a></div>
  <div class="value" style="left:203px"><div class="icon"><svg width="26" height="26"><rect x="6" y="6" width="14" height="14" fill="none" stroke="#1d1f8c" stroke-width="1.5"/></svg></div><h3>Kind People</h3><p>We NEVER talk down to others but instead choose to work harmoniously with respect and compassion.</p><a>Learn More</a></div>
  <div class="value" style="left:355px"><div class="icon"><svg width="26" height="26"><circle cx="8" cy="10" r="3" fill="none" stroke="#1d1f8c" stroke-width="1.5"/><circle cx="18" cy="10" r="3" fill="none" stroke="#1d1f8c" stroke-width="1.5"/><path d="M3 21h20" stroke="#1d1f8c" stroke-width="1.5"/></svg></div><h3>Hard Workers</h3><p>We are a team of hardworking, dedicated people who have our sights set on long-term career development.</p><a>Learn More</a></div>
  <div class="value" style="left:507px"><div class="icon"><svg width="26" height="26"><path d="M4 14l9 8 9-8M13 4v10" fill="none" stroke="#1d1f8c" stroke-width="1.5"/></svg></div><h3>Family Oriented</h3><p>We're always willing to go the extra mile for the office, share the workload, and coach one another for success.</p><a>Learn More</a></div>

  <div class="abs contact">
    <div class="abs" style="left:93px;top:42px;font-size:19px;font-weight:700">Contact Us</div>
    <svg class="abs" style="left:96px;top:88px" width="8" height="10"><path d="M4 10L1 5a3 3 0 1 1 6 0z" fill="#1d1f8c"/></svg>
    <div class="info" style="top:86px;left:111px"><b>Address</b>Lorem ipsum dolor sit amet, consectetur<br>adipiscing elit</div>
    <svg class="abs" style="left:96px;top:144px" width="8" height="8"><path d="M1 0l2 2-1 1.5a5 5 0 0 0 2.5 2.5L6 5l2 2-1.5 1C3 8 0 5 0 1.5z" fill="#1d1f8c"/></svg>
    <div class="info" style="top:142px;left:111px"><b>Phone</b>+1 888 888 8888</div>
    <svg class="abs" style="left:95px;top:190px" width="9" height="7"><rect width="9" height="7" fill="#1d1f8c"/></svg>
    <div class="info" style="top:188px;left:111px"><b>Email</b>info@company123.com</div>
    <div class="field" style="top:41px">Name</div>
    <div class="field" style="top:85px">Phone</div>
    <div class="field" style="top:128px">Email</div>
    <div class="field" style="top:171px">Message</div>
    <div class="pill" style="left:324px;top:220px;width:91px;height:30px">Submit</div>
  </div>

  <div class="abs footer" style="top:1682px">
    <svg class="abs" style="left:0;top:0" width="702" height="294" viewBox="0 0 702 294">
      <polygon points="0,0 315,57 0,50" fill="#1d1f8c"/>
      <polygon points="0,50 315,57 0,85" fill="#2233b8"/>
      <polygon points="0,85 315,57 702,50 702,294 0,294" fill="#000"/>
    </svg>
    <div class="brand">Quillbrook</div>
    <p class="abs" style="left:65px;top:162px;width:170px;font-size:8.5px;line-height:17.5px">Lorem ipsum dolor sit amet, consectetur adipiscing elit, sed do eiusmod tempor incididunt</p>
    <h4 style="left:265px">Quick Link</h4>
    <ul style="left:268px"><li>Home</li><li>Jobs</li><li>About</li><li>Contact</li></ul>
    <h4 style="left:360px">Areas we service</h4>
    <ul style="left:363px"><li>Cedar Hollow</li><li>Maple Ridge</li><li>Stonebrook</li></ul>
    <h4 style="left:487px">Get Our Newsletter</h4>
    <div class="abs" style="left:488px;top:143px;width:150px;height:21px;border:1px solid #555;border-radius:2px;font-size:8px;color:#777;padding:5px 7px">Enter Your Email
      <svg class="abs" style="right:6px;top:5px" width="9" height="9"><path d="M0 5L9 0 6 9 4 5z" fill="#2233b8"/></svg></div>
    <div class="social"><i></i><i></i><i></i><i></i></div>
    <div class="abs" style="left:65px;top:242px;width:572px;height:1px;background:#222"></div>
    <div class="abs center" style="top:262px;font-size:8px">© Copyrights 2022 My Quillbrook &nbsp; | &nbsp; All Rights Reserved</div>
  </div>
</div>

<!-- Short homepage variant -->
<div class="page page--short">
  <div class="abs topbar">
    <span style="left:67px"><svg width="9" height="9" viewBox="0 0 10 10"><path d="M2 1l2 2-1 1.5a6 6 0 0 0 2.5 2.5L7 6l2 2-1.5 1.5C4.5 9 1 5.5.5 2.5z" fill="none" stroke="#fff"/></svg>555-014-2290</span>
    <span style="left:443px"><svg width="10" height="8"><rect x=".5" y=".5" width="9" height="7" fill="none" stroke="#fff"/></svg>Pay Card Login</span>
    <span style="left:552px"><svg width="10" height="9"><path d="M0 3L5 0 10 3zM1 8h8M2 4v3M5 4v3M8 4v3" stroke="#fff" fill="#fff"/></svg>Partner Bank Login</span>
  </div>
  <div class="abs nav">
    <div class="brand" style="left:65px;top:5px">Quillbrook</div>
    <a class="active" style="left:313px">Home</a><a style="left:365px">Jobs</a><a style="left:411px">About</a><a style="left:463px">Contact</a>
    <div class="pill" style="left:539px;top:11px;width:98px;height:29px">Employee Login</div>
  </div>
  <div class="abs hero">
    <div class="hero-photo" role="img" aria-label="Photo of hands holding a document over a desk"></div>
    <svg class="abs" style="left:0;top:0" width="702" height="410" viewBox="0 0 702 410">
      <polygon points="0,351 385,335 702,404 702,412 0,412" fill="#fff"/>
      <polygon points="385,335 702,318 702,404" fill="#1d1f8c"/>
      <polygon points="385,335 702,330 702,352" fill="#2233b8"/>
    </svg>
    <div class="hero-copy" style="top:81px;font-size:11px;font-weight:700">Welcome To</div>
    <div class="hero-copy" style="top:100px;font-size:25px;font-weight:700">Quillbrook Clearical &amp; Industrial</div>
    <div class="hero-copy" style="top:138px;font-size:8.5px;line-height:15px">Lorem ipsum dolor sit amet, consectetur adipiscing elit, sed do eiusmod tempor<br>incididunt ut labore et dolore magna aliqua.</div>
    <div class="pill" style="left:238px;top:177px;width:108px;height:29px">I'm looking for a Job</div>
    <div class="pill pill--light" style="left:356px;top:177px;width:107px;height:29px">I need Employees</div>
  </div>
  <div class="abs about-photo" role="img" aria-label="Photo of business people with network icons overlay"></div>
  <p class="abs about-text">Greatest part of our daily job is that we are constantly bringing people together. Our Clients come to us in search of the perfect candidate and the job hunters approach us when they are in need of a job or looking for their next exciting role. Being able to work with and connect the two is incredibly satisfying. Not to mention that in today's current job market, employers are fighting for the top talent. This makes our employees and partners grateful for the help in finding it!</p>
  <div class="pill" style="left:305px;top:640px;width:86px;height:30px">Learn More</div>
  <div class="abs vlabel" style="left:615px;top:494px;font-size:22px">ABOUT</div>
  <div class="abs vlabel" style="left:603px;top:494px;font-size:6.5px">CLERICAL &amp; INDUSTRIAL</div>
  <div class="abs" style="left:603px;top:608px;width:4px;height:54px;background:var(--navy)"></div>

  <div class="abs footer" style="top:755px">
    <svg class="abs" style="left:0;top:0" width="702" height="294" viewBox="0 0 702 294">
      <polygon points="0,0 315,57 0,50" fill="#1d1f8c"/>
      <polygon points="0,50 315,57 0,85" fill="#2233b8"/>
      <polygon points="0,85 315,57 702,50 702,294 0,294" fill="#000"/>
    </svg>
    <div class="brand">Quillbrook</div>
    <p class="abs" style="left:65px;top:162px;width:170px;font-size:8.5px;line-height:17.5px">Lorem ipsum dolor sit amet, consectetur adipiscing elit, sed do eiusmod tempor incididunt</p>
    <h4 style="left:265px">Quick Link</h4>
    <ul style="left:268px"><li>Home</li><li>Jobs</li><li>About</li><li>Contact</li></ul>
    <h4 style="left:360px">Areas we service</h4>
    <ul style="left:363px"><li>Cedar Hollow</li><li>Maple Ridge</li><li>Stonebrook</li></ul>
    <h4 style="left:487px">Get Our Newsletter</h4>
    <div class="abs" style="left:488px;top:143px;width:150px;height:21px;border:1px solid #555;border-radius:2px;font-size:8px;color:#777;padding:5px 7px">Enter Your Email
      <svg class="abs" style="right:6px;top:5px" width="9" height="9"><path d="M0 5L9 0 6 9 4 5z" fill="#2233b8"/></svg></div>
    <div class="social"><i></i><i></i><i></i><i></i></div>
    <div class="abs" style="left:65px;top:242px;width:572px;height:1px;background:#222"></div>
    <div class="abs center" style="top:262px;font-size:8px">© Copyrights 2022 My Quillbrook &nbsp; | &nbsp; All Rights Reserved</div>
  </div>
</div>

</body>
</html>
```